Duct Manufacturing Company new to the industry needs business card and stationary design

we are sheet metal duct manufacturers looking for a business card design to fit my new business logo.
nothing to crazy that will date, but want it to stand out from the crowed.
I'm sure you guys will work it out.

Contact Information for Business Card

Glen Marsh
Director

Address
17 Dorwell St
Merrowdale NSW 2690

0438 760 514

Sales@flowbend.com.au

Font styles to use
Other font styles liked:
• BankGothic md bt

Requirements
Nice to have
• Like the idea of corner rounded to match logo
• like to keep colours flowing
• font I like sharp square not rounded

```html
<!DOCTYPE html>
<html lang="en">
<head>
<meta charset="utf-8">
<title>Flowbend Industries – Business Card</title>
<link rel="stylesheet" href="https://fonts.googleapis.com/css2?family=Lato:wght@400;700&display=swap">
<style>
  :root {
    --page-bg: #3b3b3b;
    --card-top: #050505;
    --card-mid: #1c1c1c;
    --card-bottom: #121212;
    --brand-blue: #1a6fc9;
    --brand-green: #6cc43a;
    --brand-grey: #9a9a9a;
    --text-light: #c9c9c9;
    --divider: #5a5a5a;
  }
  * { margin: 0; padding: 0; box-sizing: border-box; }
  html, body {
    width: 1200px; height: 750px; overflow: hidden;
    background: var(--page-bg);
    font-family: "Lato", Arial, sans-serif;
  }
  .card {
    position: absolute; left: 150px; top: 118px;
    width: 900px; height: 514px;
    background: linear-gradient(180deg, var(--card-top) 0%, var(--card-mid) 30%, var(--card-mid) 70%, var(--card-bottom) 100%);
    overflow: hidden;
  }
  .brand {
    position: absolute; left: 120px; top: 206px; width: 300px;
    display: flex; flex-direction: column; align-items: center; gap: 14px;
    color: var(--brand-green); font-weight: 700;
    text-align: center; letter-spacing: 3px;
  }
  .brand-mark {
    width: 28px; height: 28px; border-radius: 50%;
    background: var(--brand-green);
  }
  .brand-name { font-size: 34px; line-height: 1.15; }
  .divider {
    position: absolute; left: 469px; top: 140px;
    width: 2px; height: 262px;
    background: linear-gradient(180deg, transparent, var(--divider) 20%, var(--divider) 80%, transparent);
  }
  .contact { position: absolute; left: 519px; top: 142px; color: var(--text-light); }
  .person-name { font-size: 31px; color: var(--brand-blue); font-weight: 400; line-height: 1.2; }
  .person-role { font-size: 23px; color: var(--brand-green); line-height: 1.2; margin-bottom: 16px; }
  .address { font-size: 21px; line-height: 27px; margin-bottom: 16px; }
  .details { list-style: none; font-size: 21px; }
  .details li { display: flex; align-items: center; gap: 12px; height: 35px; }
  .details svg { width: 22px; height: 22px; fill: var(--brand-blue); flex: none; }
  .bands { position: absolute; left: 0; bottom: 0; width: 100%; height: 20px; display: flex; gap: 3px; }
  .band { flex: 1; }
  .band-green { background: linear-gradient(90deg, #4fae2c, #8ccf3c); }
  .band-blue { background: linear-gradient(90deg, #0d5fb4, #1e8fdd, #0d5fb4); }
  .band-grey { background: linear-gradient(90deg, #777, #b5b5b5, #888); }
</style>
</head>
<body>
  <div class="card">
    <div class="brand">
      <span class="brand-mark"></span>
      <span class="brand-name">FLOWBEND<br>INDUSTRIES</span>
    </div>
    <div class="divider"></div>
    <div class="contact">
      <p class="person-name">Glen Marsh</p>
      <p class="person-role">Director</p>
      <p class="address">17 Dorwell St<br>Merrowdale NSW 2690</p>
      <ul class="details">
        <li>
          <svg viewBox="0 0 24 24" aria-hidden="true"><path d="M6.6 10.8c1.4 2.8 3.8 5.1 6.6 6.6l2.2-2.2c.3-.3.7-.4 1-.2 1.1.4 2.3.6 3.6.6.6 0 1 .4 1 1V20c0 .6-.4 1-1 1C10.6 21 3 13.4 3 4c0-.6.4-1 1-1h3.5c.6 0 1 .4 1 1 0 1.3.2 2.5.6 3.6.1.3 0 .7-.2 1l-2.3 2.2z"/></svg>
          0438 760 514
        </li>
        <li>
          <svg viewBox="0 0 24 24" aria-hidden="true"><path d="M2 5h20v2l-10 7L2 7z"/><path d="M2 9l10 7 10-7v10H2z"/></svg>
          Sales@flowbend.com.au
        </li>
        <li>
          <svg viewBox="0 0 24 24" aria-hidden="true"><circle cx="12" cy="12" r="10"/><path d="M4 12h16M12 2c3 3 3 17 0 20M12 2c-3 3-3 17 0 20" stroke="#1c1c1c" stroke-width="1.5" fill="none"/></svg>
          www.flowbend.com.au
        </li>
      </ul>
    </div>
    <div class="bands">
      <span class="band band-green"></span>
      <span class="band band-blue"></span>
      <span class="band band-grey"></span>
    </div>
  </div>
</body>
</html>
```